My project benefits Military, First Responders, Police, Fire, and Educators.

Contact Information for Business Card

2 Sided appointment card. Visual side will have my head shot with "Brisk Lantern" in a bold graffic/text. I am picturing maybe the headshot applied to a filter that has a matrix effect where the picture is made up of data/numbers flowing vertically through the photo. I am of course open to other concepts as well. Side two will have contact info presented in an attractive visual complimenting the front.

```html
<!DOCTYPE html>
<html lang="en">
<head>
<meta charset="utf-8">
<title>Brisk Lantern – Appointment Card</title>
<link href="https://fonts.googleapis.com/css2?family=Open+Sans:wght@400;600;700&display=swap" rel="stylesheet">
<style>
  :root {
    --backdrop-top: #2a2a2a;
    --backdrop-bottom: #050505;
    --card: #ffffff;
    --navy: #1d3a66;
    --brand-blue: #1b78be;
    --rule-blue: #7fbbe6;
    --ink: #2b2b2b;
    --muted: #555a60;
    --portrait-light: #d9c6b6;
    --portrait-skin: #bf8f73;
    --portrait-suit: #1b2336;
  }
  * { margin: 0; padding: 0; box-sizing: border-box; }
  html, body { width: 1200px; height: 900px; overflow: hidden; }
  body {
    position: relative;
    background: linear-gradient(180deg, var(--backdrop-top) 0%, #161616 55%, var(--backdrop-bottom) 100%);
    font-family: "Open Sans", Arial, sans-serif;
    color: var(--ink);
  }
  .card {
    position: absolute;
    top: 306px;
    width: 440px;
    height: 271px;
    background: var(--card);
    border-radius: 10px;
    overflow: hidden;
  }
  .card--front { left: 149px; }
  .card--back { left: 608px; }

  .wordmark {
    position: absolute;
    color: var(--brand-blue);
    font-weight: 600;
    font-size: 30px;
    line-height: 1.05;
    letter-spacing: 1px;
    text-transform: uppercase;
  }
  .card--front .wordmark { left: 32px; top: 48px; }
  .card--back .wordmark { left: 247px; top: 52px; }
  .wordmark__dot {
    display: inline-block;
    width: 14px; height: 14px;
    border-radius: 50%;
    background: var(--brand-blue);
    margin-left: 6px;
    vertical-align: 3px;
  }

  .holder { position: absolute; left: 29px; top: 158px; }
  .holder__name { color: var(--navy); font-weight: 700; font-size: 15px; line-height: 20px; }
  .holder__role { font-size: 12px; line-height: 16px; color: var(--ink); }

  .contacts { position: absolute; left: 29px; top: 207px; list-style: none; }
  .contacts li {
    display: flex; align-items: center;
    font-size: 12px; line-height: 16px; height: 16px;
    color: var(--ink);
  }
  .contacts svg { width: 9px; height: 9px; margin-right: 8px; fill: var(--navy); flex: none; }

  .portrait {
    position: absolute;
    left: 220px; top: 12px;
    width: 220px; height: 259px;
    background: linear-gradient(180deg,
      var(--portrait-light) 0%,
      var(--portrait-skin) 38%,
      #a9876f 55%,
      #3a4560 66%,
      var(--portrait-suit) 100%);
    border-top-left-radius: 60% 45%;
    border-top-right-radius: 30% 18%;
  }

  .appointment { position: absolute; left: 39px; top: 126px; color: var(--brand-blue); font-weight: 700; font-size: 15px; }
  .appointment__line { position: absolute; left: 39px; width: 254px; height: 1px; background: var(--rule-blue); }
  .appointment__line--first { top: 183px; }
  .appointment__line--second { top: 217px; }
  .appointment__note { position: absolute; left: 38px; top: 235px; font-size: 12px; color: var(--muted); }
</style>
</head>
<body>
  <section class="card card--front">
    <div class="wordmark">Brisk<span class="wordmark__dot"></span><br>Lantern</div>

    <div class="holder">
      <p class="holder__name">Daniel Reeve</p>
      <p class="holder__role">Managing Director</p>
    </div>

    <ul class="contacts">
      <li>
        <svg viewBox="0 0 10 10"><path d="M2 0.5 L3.6 2.6 L2.8 3.6 Q4 6 6.4 7.2 L7.4 6.4 L9.5 8 L8.4 9.5 Q4.5 9.4 2 6.8 Q0.4 4.6 0.5 1.6 Z"/></svg>
        044-987 654 321
      </li>
      <li>
        <svg viewBox="0 0 10 10"><path d="M0 2 H10 V8.5 H0 Z"/><path d="M0.8 2.6 L5 5.4 L9.2 2.6" stroke="#fff" stroke-width="0.8" fill="none"/></svg>
        hello@brisklantern.com
      </li>
      <li>
        <svg viewBox="0 0 10 10"><circle cx="5" cy="5" r="4.6"/><path d="M5 0.6 V9.4 M0.6 5 H9.4 M5 0.6 Q2.4 5 5 9.4 M5 0.6 Q7.6 5 5 9.4" stroke="#fff" stroke-width="0.7" fill="none"/></svg>
        www.brisklantern.com
      </li>
    </ul>

    <div class="portrait" role="img" aria-label="Head-and-shoulders portrait of the card holder in a dark suit and striped tie"></div>
  </section>

  <section class="card card--back">
    <div class="wordmark">Brisk<span class="wordmark__dot"></span><br>Lantern</div>
    <h2 class="appointment">Appointment</h2>
    <div class="appointment__line appointment__line--first"></div>
    <div class="appointment__line appointment__line--second"></div>
    <p class="appointment__note">If unable to keep appointment, kindly give 24hrs notice.</p>
  </section>
</body>
</html>
```